Business Card Design Project

We are a construction company in Orange County, CA. We need a two sided business card. We would like the back to be our logo with web URL. Front should included Name, title, address, phone, fax and email address.

our address is
627 West Dorrance Blvd, Suite 308
Anaheim, CA 92718

Our logo files are attached.

Construction

```html
<!DOCTYPE html>
<html lang="en">
<head>
<meta charset="utf-8">
<title>Halden Business Card</title>
<link rel="stylesheet" href="https://fonts.googleapis.com/css2?family=Arimo:wght@400;700&display=swap">
<style>
  :root {
    --brand-blue: #1c4f86;
    --link-blue: #2a6fb0;
    --ink: #222222;
    --card: #ffffff;
    --backdrop: #e7e9ec;
  }
  * { box-sizing: border-box; margin: 0; padding: 0; }
  html, body { width: 1200px; height: 900px; overflow: hidden; }
  body {
    background: var(--backdrop);
    font-family: "Arimo", Arial, sans-serif;
    position: relative;
  }
  .card {
    position: absolute;
    left: 300px;
    width: 600px;
    height: 343px;
    background: var(--card);
    border-radius: 22px;
    box-shadow: 0 6px 18px rgba(0,0,0,0.18);
    overflow: hidden;
  }
  .card--back { top: 70px; }
  .card--front { top: 487px; }

  /* Back side */
  .back-band {
    position: absolute;
    left: 0; right: 0;
    top: 150px;
    height: 16px;
    background: var(--brand-blue);
  }
  .back-brand {
    position: absolute;
    left: 50%;
    top: 122px;
    transform: translateX(-50%);
    background: var(--card);
    padding: 0 14px;
    text-align: center;
  }
  .wordmark {
    font-family: "Arimo", Arial, sans-serif;
    font-weight: 700;
    color: var(--brand-blue);
    letter-spacing: 1px;
    line-height: 1;
    white-space: nowrap;
  }
  .back-brand .wordmark { font-size: 60px; }
  .back-motto {
    margin-top: 5px;
    font-size: 11px;
    letter-spacing: 3px;
    color: var(--brand-blue);
    font-weight: 700;
    white-space: nowrap;
  }
  .back-url {
    position: absolute;
    right: 36px;
    bottom: 30px;
    font-size: 15px;
    color: var(--link-blue);
  }

  /* Front side */
  .front-motto {
    position: absolute;
    left: 0;
    right: 0;
    top: 28px;
    text-align: center;
    font-size: 23px;
    letter-spacing: 7px;
    color: var(--brand-blue);
    white-space: nowrap;
  }
  .front-band {
    position: absolute;
    left: 0;
    top: 84px;
    width: 322px;
    height: 30px;
    background: var(--brand-blue);
  }
  .front-brand {
    position: absolute;
    left: 16px;
    top: 126px;
    font-size: 60px;
  }
  .contact {
    position: absolute;
    left: 334px;
    top: 90px;
    width: 250px;
  }
  .contact__name {
    font-size: 19px;
    font-weight: 700;
    color: var(--link-blue);
    border-bottom: 1.5px solid var(--link-blue);
    padding-bottom: 1px;
    width: 200px;
  }
  .contact__title {
    font-size: 11px;
    color: var(--ink);
    margin-top: 2px;
  }
  .contact__address {
    margin-top: 12px;
    font-size: 15.5px;
    line-height: 1.12;
    color: var(--link-blue);
    white-space: nowrap;
  }
  .contact__list {
    list-style: none;
    margin-top: 14px;
  }
  .contact__item {
    display: flex;
    align-items: center;
    gap: 18px;
    font-size: 17px;
    line-height: 1.35;
    color: var(--ink);
    margin-left: -18px;
  }
  .contact__icon { width: 16px; height: 16px; flex: none; fill: var(--brand-blue); }
</style>
</head>
<body>

<section class="card card--back" aria-label="Card back">
  <div class="back-band"></div>
  <div class="back-brand">
    <div class="wordmark">HALDEN</div>
    <div class="back-motto">DESIGN • BUILD • DELIVER</div>
  </div>
  <div class="back-url">www.yourdomain.com</div>
</section>

<section class="card card--front" aria-label="Card front">
  <div class="front-motto">DESIGN • BUILD • DELIVER</div>
  <div class="front-band"></div>
  <div class="front-brand wordmark">HALDEN</div>

  <div class="contact">
    <div class="contact__name">Marcus Delaney</div>
    <div class="contact__title">General Manager</div>
    <div class="contact__address">627 West Dorrance Blvd, Suite 308<br>Anaheim, CA 92718</div>
    <ul class="contact__list">
      <li class="contact__item">
        <svg class="contact__icon" viewBox="0 0 16 16" aria-hidden="true"><path d="M1 6c0-2 3-3 7-3s7 1 7 3l-3 1-1-2H5L4 7z"/><rect x="3" y="8" width="10" height="6" rx="1.5"/></svg>
        (00) 123-4567-890
      </li>
      <li class="contact__item">
        <svg class="contact__icon" viewBox="0 0 16 16" aria-hidden="true"><rect x="4" y="1" width="8" height="5"/><rect x="1" y="6" width="14" height="9" rx="1.5"/><rect x="4" y="9" width="8" height="1.5" fill="#fff"/><rect x="4" y="12" width="8" height="1.5" fill="#fff"/></svg>
        (00) 123-4567-890
      </li>
      <li class="contact__item">
        <svg class="contact__icon" viewBox="0 0 16 16" aria-hidden="true"><path d="M1 6l7-5 7 5v8H1z"/><path d="M2 7l6 4 6-4" stroke="#fff" stroke-width="1.3" fill="none"/></svg>
        info@yourdomain.com
      </li>
      <li class="contact__item">
        <svg class="contact__icon" viewBox="0 0 16 16" aria-hidden="true"><circle cx="8" cy="8" r="7"/><g stroke="#fff" stroke-width="1" fill="none"><ellipse cx="8" cy="8" rx="3" ry="7"/><path d="M1 8h14M2.5 4.5h11M2.5 11.5h11"/></g></svg>
        www.yourdomain.com
      </li>
    </ul>
  </div>
</section>

</body>
</html>
```